Stationary design for boutique production house

We need a stationary design for our production house, 'Lorno Productions' based in Singapore. We produce microfilms as well as podcasts, talkshows and events. Our logo is a stylized icon of our director, who is also the executive producer and host of our programs, Lorno. Our main company colors are Red, Black and white. We would like a clean, minimalist design incorporating our existing company logo that conveys a sense of urbanism and elegance.

Logo and font files are attached. f

Target Market(s)

We focus on lifestyle media rather than entertainment.

Industry/Entity Type

Boutique

Font styles to use
Serif
Sans Serif

Colors
ec1f27
ffffff
000000

Requirements
Must have
• Our company logo and at least one of our company colors.
Nice to have
• Our address and contact information.
Should not have
• Changes made to the company logo (using only certain parts of it is fine though)

```html
<!DOCTYPE html>
<html lang="en">
<head>
<meta charset="utf-8">
<title>Lorno Productions — Stationery</title>
<link rel="stylesheet" href="https://fonts.googleapis.com/css2?family=Source+Sans+3:wght@300;400;600&display=swap">
<style>
  :root {
    --red: #ec1f27;
    --black: #231f20;
    --white: #ffffff;
    --paper: #f6f5f3;
    --backdrop: #aaa9aa;
    --ink: #3a3a3a;
    --shadow: 0 3px 8px rgba(0,0,0,.28);
  }
  * { box-sizing: border-box; margin: 0; padding: 0; }
  html, body { width: 1123px; height: 1200px; overflow: hidden; }
  body { background: var(--backdrop); font-family: "Source Sans 3", sans-serif; color: var(--ink); position: relative; }
  .sheet { position: absolute; box-shadow: var(--shadow); }

  .wordmark { font-family: "Source Sans 3", sans-serif; font-weight: 600; letter-spacing: .06em; line-height: 1.05; text-transform: uppercase; display: flex; align-items: center; gap: 6px; }
  .wordmark .dot { width: 8px; height: 8px; border-radius: 50%; background: var(--red); flex: none; }

  /* Letterhead */
  .letterhead { left: 62px; top: 34px; width: 510px; height: 718px; background: var(--paper); }
  .letterhead .wordmark { position: absolute; left: 50px; top: 100px; font-size: 13px; color: var(--black); }
  .contact { position: absolute; left: 358px; top: 52px; font-size: 8.6px; font-weight: 300; line-height: 11px; color: var(--ink); }
  .contact .lines { margin-top: 7px; }
  .contact .row { display: flex; align-items: center; gap: 5px; height: 12px; }
  .contact svg { width: 7px; height: 7px; fill: var(--red); flex: none; }
  .salutation { position: absolute; left: 51px; top: 225px; font-size: 13.5px; font-weight: 400; color: var(--ink); }
  .body { position: absolute; left: 51px; top: 271px; width: 412px; font-size: 7.3px; line-height: 12.3px; color: var(--ink); text-align: justify; }
  .body p { margin-bottom: 12.3px; }
  .signoff { position: absolute; left: 51px; top: 501px; font-size: 7.5px; }
  .signature { position: absolute; left: 48px; top: 516px; width: 68px; height: 26px; }
  .signer { position: absolute; left: 54px; top: 553px; font-size: 8px; line-height: 13.5px; }
  .footer { position: absolute; left: 50px; right: 49px; top: 679px; display: flex; align-items: center; gap: 6px; font-size: 7.6px; letter-spacing: .38em; font-weight: 300; white-space: nowrap; }
  .footer::before, .footer::after { content: ""; flex: 1; height: 1px; background: currentColor; opacity: .8; }

  /* Folder */
  .folder { left: 588px; top: 34px; width: 510px; height: 718px; background: var(--red); color: var(--white); }
  .folder .emblem { position: absolute; left: 243px; top: 346px; width: 24px; height: 24px; border-radius: 50%; background: var(--white); }
  .folder .wordmark { position: absolute; left: 0; right: 0; top: 398px; justify-content: center; flex-direction: column; font-size: 28px; text-align: center; color: var(--white); }

  /* Envelope */
  .envelope-back { left: 144px; top: 778px; width: 573px; height: 261px; background: var(--paper); }
  .envelope-back svg.flap { position: absolute; left: 0; top: 0; width: 573px; height: 97px; }
  .envelope-back .flap-dot { position: absolute; left: 279px; top: 41px; width: 14px; height: 14px; border-radius: 50%; background: var(--white); }
  .envelope-front { left: 73px; top: 894px; width: 574px; height: 261px; background: var(--paper); }
  .envelope-front .wordmark { position: absolute; left: 29px; top: 72px; font-size: 9.5px; color: var(--black); gap: 4px; }
  .envelope-front .wordmark .dot { width: 6px; height: 6px; }
  .envelope-front .address { position: absolute; left: 28px; top: 118px; font-size: 9px; font-weight: 300; line-height: 10.5px; }

  /* Business cards */
  .card { top: 873px; width: 128px; height: 224px; }
  .card-front { left: 772px; background: var(--white); text-align: center; }
  .card-front .wordmark { position: absolute; left: 0; right: 0; top: 62px; justify-content: center; font-size: 8px; color: var(--black); gap: 3px; }
  .card-front .wordmark .dot { width: 5px; height: 5px; }
  .card-front .name { position: absolute; left: 0; right: 0; top: 119px; font-size: 8px; color: var(--red); line-height: 8.5px; }
  .card-front .role { position: absolute; left: 0; right: 0; top: 128px; font-size: 6px; color: var(--ink); }
  .card-front .addr { position: absolute; left: 0; right: 0; top: 143px; font-size: 5px; line-height: 7px; font-weight: 300; }
  .card-front .lines { position: absolute; left: 0; right: 0; top: 162px; font-size: 5px; line-height: 9px; font-weight: 300; }
  .card-front .lines span { display: inline-flex; align-items: center; gap: 2px; }
  .card-front .lines svg { width: 5px; height: 5px; fill: var(--red); }
  .card-back { left: 918px; background: var(--red); color: var(--white); text-align: center; }
  .card-back .wordmark { position: absolute; left: 0; right: 0; top: 36px; flex-direction: column; font-size: 11px; color: var(--white); gap: 3px; }
  .card-back .web { position: absolute; left: 0; right: 0; top: 80px; font-size: 5px; letter-spacing: .3em; font-weight: 300; }
  .card-back .disc { position: absolute; left: 44px; top: 152px; width: 40px; height: 40px; border-radius: 50%; background: var(--white); }
</style>
</head>
<body>

<svg width="0" height="0" style="position:absolute">
  <symbol id="i-phone" viewBox="0 0 10 10"><path d="M2 0.5 L3.6 2.6 L2.6 3.6 Q3.6 5.8 6.4 7.4 L7.4 6.4 L9.5 8 L8.3 9.5 Q2.5 8.6 0.5 1.7 Z"/></symbol>
  <symbol id="i-mobile" viewBox="0 0 10 10"><path d="M2.5 0 H7.5 V10 H2.5 Z M3.3 1 V8.4 H6.7 V1 Z"/></symbol>
  <symbol id="i-fax" viewBox="0 0 10 10"><path d="M2.5 0 H7.5 V3 H2.5 Z M0 3.5 H10 V8 H0 Z M2 8.5 H8 V10 H2 Z"/></symbol>
  <symbol id="i-mail" viewBox="0 0 10 10"><path d="M0 2 H10 V8 H0 Z M0.8 2.6 L5 5.6 L9.2 2.6 Z"/></symbol>
  <symbol id="i-web" viewBox="0 0 10 10"><circle cx="5" cy="5" r="4.5"/></symbol>
</svg>

<!-- Letterhead -->
<section class="sheet letterhead">
  <div class="wordmark"><span class="dot"></span>Lorno Productions</div>
  <div class="contact">
    <div>4120 Harbour Walk<br>Singapore 098632</div>
    <div class="lines">
      <div class="row"><svg><use href="#i-phone"/></svg>612 480 3175</div>
      <div class="row"><svg><use href="#i-mobile"/></svg>845 219 7703</div>
      <div class="row"><svg><use href="#i-fax"/></svg>427 903 5618</div>
      <div class="row"><svg><use href="#i-mail"/></svg>hello@lornoprod.sg</div>
    </div>
  </div>
  <div class="salutation">Dear Mr. Smith,</div>
  <div class="body">
    <p>Lorem ipsum dolor sit amet, consectetur adipiscing elit. Donec orci purus, luctus vitae dignissim eu, iaculis sed purus. Vivamus faucibus, ipsum nec aliquet viverra, leo mauris condimentum ligula, sit amet sagittis enim ligula quis arcu. Nam egestas tortor id nisi porttitor mattis. In tortor ante, ultricies in suscipit a, tempus non massa. Vivamus et auctor mi. Fusce vel massa nulla. Phasellus nec eros mauris, et scelerisque orci.</p>
    <p>Donec malesuada orci vitae nulla accumsan porta a id massa. Quisque accumsan iaculis magna sit amet fringilla. Maecenas consequat, magna eget tincidunt semper, odio nibh rutrum mi, id feugiat ante nisi eu risus. Vestibulum nunc orci, rhoncus a placerat in, ultricies in mi. Cras mattis varius eros, vel fringilla nisi suscipit eget. Quisque scelerisque sagittis nulla at porttitor.</p>
    <p>Sed id augue vitae urna euismod commodo aliquet a quam. Pellentesque arcu velit, cursus et malesuada ut, consequat et diam. Nullam erat sem, rhoncus id ullamcorper vitae, rhoncus et arcu. In ultricies ultricies nulla, ut rutrum nisi iaculis at. Donec eu magna a metus ornare faucibus. Fusce aliquet faucibus ultricies. Morbi semper, est id tincidunt gravida, sem arcu adipiscing lacus, ac bibendum nulla leo eu purus. Quisque nec diam sed risus consectetur a cumsan quis quis nibh. Vestibulum id purus lorem.</p>
    <p>It is a long established fact that a reader will be distracted by the readable content of a page when looking at its layout. The point of using Lorem Ipsum is that it has a more-or-less normal distribution of letters, as opposed to using 'Content here, content here', making it look like readable English. Many desktop publishing packages</p>
  </div>
  <div class="signoff">Sincerely,</div>
  <svg class="signature" viewBox="0 0 68 26" fill="none" stroke="#1c1c2a" stroke-width="1.1">
    <path d="M1 13 Q30 9 66 14 M6 11 Q24 2 44 10 Q40 12 30 15 M38 9 Q45 16 49 24"/>
  </svg>
  <div class="signer">Daniel Tan<br>CEO/ Founder</div>
  <div class="footer">www.lornoprod.sg</div>
</section>

<!-- Presentation folder -->
<section class="sheet folder">
  <div class="emblem"></div>
  <div class="wordmark"><span>Lorno</span><span>Productions</span></div>
  <div class="footer">www.lornoprod.sg</div>
</section>

<!-- Envelope (back with flap) -->
<section class="sheet envelope-back">
  <svg class="flap" viewBox="0 0 573 97" preserveAspectRatio="none">
    <path d="M0 0 H573 L559 70 Q554 92 532 92 H45 Q22 92 17 70 Z" fill="#ec1f27"/>
  </svg>
  <div class="flap-dot"></div>
</section>

<!-- Envelope (front) -->
<section class="sheet envelope-front">
  <div class="wordmark"><span class="dot"></span>Lorno Productions</div>
  <div class="address">4120 Harbour Walk<br>Harbourfront<br>Singapore 098632</div>
</section>

<!-- Business card front -->
<section class="sheet card card-front">
  <div class="wordmark"><span class="dot"></span>Lorno Productions</div>
  <div class="name">DANIEL TAN</div>
  <div class="role">CEO/FOUNDER</div>
  <div class="addr">4120 Harbour Walk<br>Singapore 098632</div>
  <div class="lines">
    <span><svg><use href="#i-phone"/></svg>612 480 3175</span><br>
    <span><svg><use href="#i-mobile"/></svg>845 219 7703</span><br>
    <span><svg><use href="#i-fax"/></svg>427 903 5618</span><br>
    <span><svg><use href="#i-mail"/></svg>hello@lornoprod.sg</span><br>
    <span><svg><use href="#i-web"/></svg>www.lornoprod.sg</span>
  </div>
</section>

<!-- Business card back -->
<section class="sheet card card-back">
  <div class="wordmark"><span>Lorno</span><span>Productions</span></div>
  <div class="web">www.lornoprod.sg</div>
  <div class="disc"></div>
</section>

</body>
</html>
```